Navoro & Omvar Automotive Repair Shop. Need a new website design.

We specialize in Navoro & Omvar auto repair, but also work on other Asian import vehicles. We have been in business for 7 years and pride ourselves on high quality auto repair that is fixed right the first time. Would like the automotive repair website to incorporate the colors black, red and white if possible and have our logo and some Navoro and Omvar vehicles included in the website.

Target Market(s)

Navoro & Omvar vehicle owners

Industry/Entity Type

Automotive Repair

Coding

Coded - Design and coding required

Number of Pages Required

5+ page

Colors
EB3D1F
EC4F4E
F09395
F8D3D4
FCEDEE

Requirements
Must have
• Home, Services, Contact Us, Schedule appointment, and a gallery tab that I can add shop pictures to when completed.
Nice to have
• Would like to see example pictures of job next to each service listed.
Should not have
• Service not related to auto repair. Ex. auto detailing, towing, car wash

```html
<!DOCTYPE html>
<html lang="en">
<head>
<meta charset="utf-8">
<title>Corvel Automotive – Services</title>
<link href="https://fonts.googleapis.com/css2?family=Fira+Sans+Condensed:ital,wght@0,500;0,600;0,700;1,500&family=Open+Sans:ital,wght@0,400;0,600;0,700;1,400&display=swap" rel="stylesheet">
<style>
:root{
  --red:#e3020f;
  --red-dark:#b8000b;
  --black:#0b0b0b;
  --ink:#1a1a1a;
  --text:#3a3a3a;
  --muted:#8c8c8c;
  --line:#e8e8e8;
  --white:#ffffff;
  --footer:#141414;
}
*{box-sizing:border-box;margin:0;padding:0}
html,body{width:1200px;height:2463px;overflow:hidden}
body{position:relative;background:var(--white);font-family:"Open Sans",sans-serif;color:var(--text)}
.abs{position:absolute}
.cond{font-family:"Fira Sans Condensed",sans-serif}

/* header */
.site-header{position:absolute;left:0;top:0;width:1200px;height:122px;background:var(--black)}
.header-rule{position:absolute;left:0;top:119px;width:360px;height:3px;background:var(--red)}
.brand{position:absolute;left:122px;top:40px;color:var(--white);font-family:"Fira Sans Condensed",sans-serif;font-weight:700;font-size:26px;letter-spacing:1px;line-height:1}
.brand small{display:block;font-size:26px}
.top-info{position:absolute;top:20px;display:flex;align-items:center;gap:10px;color:var(--white);font-style:italic;font-size:13px;line-height:17px}
.top-info .badge{width:36px;height:36px;border-radius:50%;background:#d9d9d9;display:flex;align-items:center;justify-content:center}
.top-info .accent{color:var(--red);font-weight:600}
.stars{color:var(--red);font-style:normal;font-size:15px;letter-spacing:1px}
.main-nav{position:absolute;top:95px;right:112px;display:flex;gap:32px;font-weight:700;font-size:11.5px;color:var(--white);letter-spacing:.2px}
.main-nav .active{color:var(--red)}

/* hero */
.hero{position:absolute;left:0;top:122px;width:1200px;height:315px;background:linear-gradient(90deg,#3a1d1f 0%,#4a2a2c 30%,#2b2b2d 55%,#1b1b1c 100%)}
.hero-tint{position:absolute;left:0;top:0;width:620px;height:315px;background:linear-gradient(90deg,rgba(150,20,25,.55),rgba(120,20,25,0))}
.hero-eyebrow{position:absolute;left:113px;top:75px;color:var(--white);font-size:11px;font-weight:600;letter-spacing:.6px;display:flex;align-items:center;gap:14px;font-family:"Fira Sans Condensed",sans-serif}
.hero-eyebrow::before{content:"";width:40px;height:1px;background:var(--white)}
.hero h1{position:absolute;left:111px;top:92px;color:var(--white);font-family:"Fira Sans Condensed",sans-serif;font-weight:600;font-size:50px;line-height:52px}
.hero h1 .mark{text-decoration:underline;text-decoration-color:var(--red);text-decoration-thickness:3px;text-underline-offset:6px}
.hero p{position:absolute;left:111px;top:208px;width:320px;color:var(--white);font-size:11.5px;line-height:17px}
.hero-band{position:absolute;left:0;top:436px}

/* intro */
.eyebrow{display:flex;align-items:center;gap:12px;color:var(--red);font-family:"Fira Sans Condensed",sans-serif;font-weight:600;font-size:11px;letter-spacing:.5px}
.eyebrow::before{content:"";width:40px;height:1px;background:var(--red)}
.intro-title{position:absolute;left:212px;top:565px;font-family:"Fira Sans Condensed",sans-serif;font-weight:600;font-size:36px;line-height:37px;color:var(--ink)}
.intro-sub{position:absolute;left:212px;top:688px;font-family:"Fira Sans Condensed",sans-serif;font-style:italic;font-weight:500;font-size:18px;color:var(--ink)}
.intro-copy{position:absolute;left:558px;top:541px;width:425px;font-size:11.4px;line-height:20px;color:#4a4a4a}
.btn-appoint{position:absolute;left:558px;top:689px;width:212px;height:44px;background:var(--red);color:var(--white);font-family:"Fira Sans Condensed",sans-serif;font-weight:700;font-size:12px;letter-spacing:.3px;display:flex;align-items:center;justify-content:center;gap:6px;clip-path:polygon(14px 0,100% 0,100% 100%,0 100%,0 14px)}
.call{position:absolute;left:787px;top:691px;display:flex;align-items:center;gap:10px}
.call .ring{width:42px;height:42px;border:2px solid var(--ink);border-radius:50%;display:flex;align-items:center;justify-content:center}
.call small{display:block;font-family:"Fira Sans Condensed",sans-serif;font-weight:500;font-size:12px;color:var(--ink)}
.call strong{display:block;font-family:"Fira Sans Condensed",sans-serif;font-weight:600;font-size:22px;color:var(--ink);line-height:24px}

/* services grid */
.service{position:absolute;width:235px;height:327px;border:1px solid var(--line);background:var(--white)}
.service .icon{position:absolute;left:17px;top:-21px;width:42px;height:42px;background:#8d8d8d;display:flex;align-items:center;justify-content:center}
.service h3{position:absolute;left:16px;top:36px;font-family:"Fira Sans Condensed",sans-serif;font-weight:600;font-size:15px;color:var(--ink)}
.service p{position:absolute;left:17px;top:60px;width:205px;font-size:11.4px;line-height:16px;color:#333}
.service .more{position:absolute;left:17px;top:105px;font-family:"Fira Sans Condensed",sans-serif;font-weight:600;font-size:11px;color:var(--muted);border-bottom:1px solid var(--muted);padding-bottom:2px}
.service .photo{position:absolute;left:-1px;top:143px;width:235px;height:183px}
.service.featured{background:var(--red);border-color:var(--red)}
.service.featured .icon{background:var(--black)}
.service.featured h3,.service.featured p,.service.featured .more{color:var(--white);border-color:var(--white)}

/* pagination */
.pager{position:absolute;left:540px;top:1973px;display:flex;align-items:center;gap:12px;font-size:12px;color:var(--ink)}
.pager .dot{width:24px;height:24px;border-radius:50%;display:flex;align-items:center;justify-content:center}
.pager .prev{background:var(--red)}
.pager .next{background:#e6e6e6}
.pager span.dim{color:var(--muted)}

/* footer */
.site-footer{position:absolute;left:0;top:2062px;width:1200px;height:401px;background:var(--footer)}
.foot-brand{position:absolute;left:113px;top:135px;color:var(--white);font-family:"Fira Sans Condensed",sans-serif;font-weight:700;font-size:34px;line-height:36px;letter-spacing:1px}
.partners{position:absolute;left:113px;top:234px;display:grid;grid-template-columns:92px 76px;gap:5px}
.partners i{display:block;height:36px;background:var(--white);border-radius:2px}
.foot-heading{position:absolute;top:61px;color:var(--red);font-family:"Fira Sans Condensed",sans-serif;font-weight:600;font-size:19px}
.quick-links{position:absolute;left:367px;top:107px;list-style:none;color:var(--white);font-size:11.5px;line-height:32px}
.contact-list{position:absolute;left:506px;top:107px;list-style:none;color:var(--white);font-size:11.5px;line-height:16px}
.contact-list li{display:flex;align-items:center;gap:14px;position:absolute;left:0;width:260px}
.contact-list .ic{flex:0 0 30px;height:30px;border-radius:50%;background:#d9d9d9;display:flex;align-items:center;justify-content:center}
.contact-list .label{color:var(--red)}
.map{position:absolute;left:792px;top:63px;width:295px;height:210px;background:linear-gradient(135deg,#e9eef2,#d7e3ea);clip-path:polygon(52px 0,100% 0,100% 100%,0 100%,0 52px)}
.socials{position:absolute;left:151px;top:364px;display:flex;gap:5px}
.socials i{display:block;width:28px;height:28px;border-radius:50%;background:#d0d0d0}
.copyright{position:absolute;left:0;top:2420px;width:1200px;height:43px}
.copyright p{position:absolute;right:111px;top:16px;color:var(--white);font-size:11.5px;font-weight:600}
</style>
</head>
<body>

<header class="site-header">
  <div class="brand">CORVEL<small>AUTOMOTIVE</small></div>
  <svg class="abs" style="left:330px;top:80px" width="40" height="42" viewBox="0 0 40 42"><polygon points="26,0 40,0 14,42 0,42" fill="#e3020f"/><polygon points="34,0 40,0 16,42 10,42" fill="#d9d9d9"/></svg>
  <div class="header-rule"></div>

  <div class="top-info" style="left:519px">
    <span class="badge"><svg width="18" height="18" viewBox="0 0 18 18"><circle cx="9" cy="7" r="5" fill="none" stroke="#333" stroke-width="1.6"/><path d="M6 11 5 17 9 15 13 17 12 11" fill="none" stroke="#333" stroke-width="1.4"/></svg></span>
    <span><span class="stars">★★★★★</span><br>5 Star Service</span>
  </div>
  <div class="top-info" style="left:716px">
    <span class="badge"><svg width="18" height="18" viewBox="0 0 18 18"><path d="M3 3 15 15M15 3 3 15" stroke="#333" stroke-width="2"/></svg></span>
    <span>Quality Service<br><span class="accent">Guarantee</span></span>
  </div>
  <div class="top-info" style="left:921px">
    <span class="badge"><svg width="18" height="18" viewBox="0 0 24 24"><path d="M6 3 9 3 11 8 8 10C9.5 13 11 14.5 14 16L16 13 21 15 21 18C21 19.5 19.5 21 18 21 10 20 4 14 3 6 3 4.5 4.5 3 6 3Z" fill="#333"/></svg></span>
    <span>Call Us For Booking<br><span class="accent">555.318.4720</span></span>
  </div>

  <nav class="main-nav">
    <span>HOME</span><span>ABOUT US</span><span class="active">SERVICES ⌄</span><span>GALLERY</span><span>TESTIMONIALS</span><span>CONTACT US</span>
  </nav>
</header>

<section class="hero">
  <div role="img" aria-label="Mechanic pouring fresh oil into a car engine" style="position:absolute;inset:0;background:linear-gradient(90deg,#5a2a2c 0%,#3a3034 40%,#262628 70%,#1a1a1b 100%)"></div>
  <div class="hero-tint"></div>
  <div class="hero-eyebrow">SERVICES</div>
  <h1>Have an <span class="mark">issue</span><br>with your car?</h1>
  <p>Quisque lorem neque, ultricies eget risus quis, fringilla interdum augue. Donec sollicitudin in ante sed consequat.</p>
</section>
<svg class="hero-band" width="1200" height="40" viewBox="0 0 1200 40"><polygon points="330,0 1200,0 1200,30 1075,30 960,18 380,38" fill="#e3020f"/></svg>

<section>
  <div class="eyebrow abs" style="left:212px;top:541px">SERVICES</div>
  <h2 class="intro-title">We are The Trusted<br>Car Repair Company<br>in Your City</h2>
  <div class="intro-sub">Services We Provide</div>
  <svg class="abs" style="left:330px;top:695px" width="55" height="82" viewBox="0 0 55 82"><path d="M22 4C45 8 50 30 35 40 25 46 20 36 30 34 40 33 36 52 24 58 14 63 8 70 5 78" fill="none" stroke="#e3020f" stroke-width="1.2" stroke-dasharray="3 3"/><path d="M1 72 5 80 10 74" fill="#e3020f"/></svg>
  <p class="intro-copy">Lorem ipsum dolor sit amet, consectetur adipiscing elit. Ut non ipsum eleifend turpis vulputate pulvinar sit amet quis nulla. Vestibulum luctus nibh ligula, nec condimentum velit facilisis a. Nam cursus eu turpis a ligula. Ut efficitur tortor hendrerit dui condimentum, quis volutpat nisl dapibus. Pellentesque vel magna feugiat, pretium nunc at, rhoncus ante. Ut sagittis lorem quis leo dapibus, et mollis enim finibus. Mauris scelerisque sodales nibh eget pretium.</p>
  <div class="btn-appoint"><svg width="12" height="12" viewBox="0 0 12 12"><rect x="1" y="1" width="10" height="10" fill="none" stroke="#fff" stroke-width="1.5"/><path d="M3 6 5 8 9 3" fill="none" stroke="#fff" stroke-width="1.5"/></svg>SCHEDULE AN APPOINTMENT</div>
  <div class="call">
    <span class="ring"><svg width="20" height="20" viewBox="0 0 24 24"><path d="M6 3 9 3 11 8 8 10C9.5 13 11 14.5 14 16L16 13 21 15 21 18C21 19.5 19.5 21 18 21 10 20 4 14 3 6 3 4.5 4.5 3 6 3Z" fill="#1a1a1a"/></svg></span>
    <span><small>Requesting A Call:</small><strong>555.318.4720</strong></span>
  </div>
</section>

<section class="services">
  <!-- row 1 -->
  <article class="service" style="left:113px;top:831px">
    <span class="icon"><svg width="22" height="22" viewBox="0 0 22 22"><rect x="3" y="9" width="16" height="7" rx="2" fill="#fff"/><circle cx="7" cy="17" r="2" fill="#fff"/><circle cx="15" cy="17" r="2" fill="#fff"/></svg></span>
    <h3>Emission Repair &amp; Catalytic...</h3>
    <p>Quisque lorem neque, ultricies eget risus quis, fringilla interdu.</p>
    <span class="more">+ READ MORE</span>
    <div class="photo" role="img" aria-label="Transmission unit on a jack in a repair bay" style="background:linear-gradient(135deg,#6b6f74,#3b3e42)"></div>
  </article>
  <article class="service featured" style="left:360px;top:831px">
    <span class="icon"><svg width="22" height="22" viewBox="0 0 22 22"><rect x="3" y="10" width="14" height="8" rx="1" fill="#fff"/><path d="M18 6 14 10" stroke="#fff" stroke-width="2"/><circle cx="18" cy="5" r="1.5" fill="#fff"/></svg></span>
    <h3>Oil Changes</h3>
    <p>Quisque lorem neque, ultricies eget risus quis, fringilla interdu.</p>
    <span class="more">+ READ MORE</span>
    <div class="photo" role="img" aria-label="Golden motor oil pouring into an engine" style="background:linear-gradient(135deg,#2d3a52,#8a6a25 55%,#2a2a2c)"></div>
  </article>
  <article class="service" style="left:607px;top:831px">
    <span class="icon"><svg width="22" height="22" viewBox="0 0 22 22"><rect x="6" y="2" width="10" height="18" rx="4" fill="none" stroke="#fff" stroke-width="2"/><path d="M6 7h10M6 11h10M6 15h10" stroke="#fff" stroke-width="1.5"/></svg></span>
    <h3>Tire Balance &amp; Rotations</h3>
    <p>Quisque lorem neque, ultricies eget risus quis, fringilla interdu.</p>
    <span class="more">+ READ MORE</span>
    <div class="photo" role="img" aria-label="Silver car raised on a two-post lift" style="background:linear-gradient(135deg,#9aa3ab,#4b5563)"></div>
  </article>
  <article class="service" style="left:853px;top:831px">
    <span class="icon"><svg width="22" height="22" viewBox="0 0 22 22"><rect x="3" y="4" width="16" height="11" rx="1" fill="none" stroke="#fff" stroke-width="2"/><path d="M7 19h8" stroke="#fff" stroke-width="2"/></svg></span>
    <h3>Computer Diagnostics</h3>
    <p>Quisque lorem neque, ultricies eget risus quis, fringilla interdu.</p>
    <span class="more">+ READ MORE</span>
    <div class="photo" role="img" aria-label="Technician running diagnostics on a laptop inside a car" style="background:linear-gradient(135deg,#3b3f48,#6d7380)"></div>
  </article>

  <!-- row 2 -->
  <article class="service" style="left:113px;top:1214px">
    <span class="icon"><svg width="22" height="22" viewBox="0 0 22 22"><ellipse cx="11" cy="11" rx="6" ry="9" fill="none" stroke="#fff" stroke-width="2"/><ellipse cx="11" cy="11" rx="2.5" ry="4" fill="#fff"/></svg></span>
    <h3>Tires</h3>
    <p>Quisque lorem neque, ultricies eget risus quis, fringilla interdu.</p>
    <span class="more">+ READ MORE</span>
    <div class="photo" role="img" aria-label="Gloved hand measuring tire tread depth" style="background:linear-gradient(135deg,#c9ced4,#2a2c30)"></div>
  </article>
  <article class="service" style="left:360px;top:1214px">
    <span class="icon"><svg width="22" height="22" viewBox="0 0 22 22"><rect x="4" y="2" width="12" height="17" fill="none" stroke="#fff" stroke-width="2"/><path d="M7 7h6M7 11h6" stroke="#fff" stroke-width="1.5"/><circle cx="16" cy="16" r="4" fill="#fff"/></svg></span>
    <h3>Insurance Claims</h3>
    <p>Quisque lorem neque, ultricies eget risus quis, fringilla interdu.</p>
    <span class="more">+ READ MORE</span>
    <div class="photo" role="img" aria-label="Printed car insurance claim form with a pen" style="background:linear-gradient(135deg,#f1f2f4,#c7cbd1)"></div>
  </article>
  <article class="service" style="left:607px;top:1214px">
    <span class="icon"><svg width="22" height="22" viewBox="0 0 22 22"><path d="M3 14 6 8h10l3 6v4H3z" fill="#fff"/><circle cx="11" cy="5" r="2" fill="#fff"/></svg></span>
    <h3>Heating &amp; AC Repair</h3>
    <p>Quisque lorem neque, ultricies eget risus quis, fringilla interdu.</p>
    <span class="more">+ READ MORE</span>
    <div class="photo" role="img" aria-label="Hands holding blue and red AC pressure gauges" style="background:linear-gradient(135deg,#30404f,#6a2a2e 60%,#1c1c1e)"></div>
  </article>
  <article class="service" style="left:853px;top:1214px">
    <span class="icon"><svg width="22" height="22" viewBox="0 0 22 22"><circle cx="11" cy="11" r="8" fill="none" stroke="#fff" stroke-width="2"/><circle cx="11" cy="11" r="3" fill="#fff"/></svg></span>
    <h3>Brakes Service &amp; Repair</h3>
    <p>Quisque lorem neque, ultricies eget risus quis, fringilla interdu.</p>
    <span class="more">+ READ MORE</span>
    <div class="photo" role="img" aria-label="Mechanic inspecting a brake disc assembly" style="background:linear-gradient(135deg,#3a3d44,#8e9299)"></div>
  </article>

  <!-- row 3 -->
  <article class="service" style="left:113px;top:1604px">
    <span class="icon"><svg width="22" height="22" viewBox="0 0 22 22"><path d="M3 14 6 8h10l3 6v4H3z" fill="#fff"/><path d="M12 2 9 7h3l-2 4" fill="none" stroke="#fff" stroke-width="1.5"/></svg></span>
    <h3>Electrical Specialists</h3>
    <p>Quisque lorem neque, ultricies eget risus quis, fringilla interdu.</p>
    <span class="more">+ READ MORE</span>
    <div class="photo" role="img" aria-label="Technician working on wiring under a car dashboard" style="background:linear-gradient(135deg,#45484e,#2f5a8c)"></div>
  </article>
  <article class="service" style="left:360px;top:1604px">
    <span class="icon"><svg width="22" height="22" viewBox="0 0 22 22"><circle cx="13" cy="9" r="6" fill="none" stroke="#fff" stroke-width="2"/><path d="M9 13 3 19" stroke="#fff" stroke-width="2.5"/><path d="M10 9l2 2 4-4" fill="none" stroke="#fff" stroke-width="1.5"/></svg></span>
    <h3>Pre Purchase Inspections</h3>
    <p>Quisque lorem neque, ultricies eget risus quis, fringilla interdu.</p>
    <span class="more">+ READ MORE</span>
    <div class="photo" role="img" aria-label="Salesperson with a clipboard speaking with a couple at a dealership" style="background:linear-gradient(135deg,#2b3140,#b6bcc6)"></div>
  </article>
  <article class="service" style="left:607px;top:1604px">
    <span class="icon"><svg width="22" height="22" viewBox="0 0 22 22"><rect x="5" y="7" width="12" height="9" fill="#fff"/><path d="M2 10h3M17 10h3M9 4h4" stroke="#fff" stroke-width="2"/></svg></span>
    <h3>Engine Repair</h3>
    <p>Quisque lorem neque, ultricies eget risus quis, fringilla interdu.</p>
    <span class="more">+ READ MORE</span>
    <div class="photo" role="img" aria-label="Mechanic's hand on an open car engine" style="background:linear-gradient(135deg,#3a3b3e,#1b1b1d)"></div>
  </article>
  <article class="service" style="left:853px;top:1604px">
    <span class="icon"><svg width="22" height="22" viewBox="0 0 22 22"><path d="M4 18 18 4" stroke="#fff" stroke-width="4"/><path d="M7 11l4 4M10 8l4 4" stroke="#8d8d8d" stroke-width="1.5"/></svg></span>
    <h3>Suspension Service &amp; Repair</h3>
    <p>Quisque lorem neque, ultricies eget risus quis, fringilla interdu.</p>
    <span class="more">+ READ MORE</span>
    <div class="photo" role="img" aria-label="Mechanic working beneath a lifted vehicle" style="background:linear-gradient(135deg,#6a6d72,#2b2c30)"></div>
  </article>

  <div class="pager">
    <span class="dot prev"><svg width="8" height="10" viewBox="0 0 8 10"><path d="M6 1 2 5 6 9" fill="none" stroke="#fff" stroke-width="1.6"/></svg></span>
    <span>01<span class="dim">....02</span></span>
    <span class="dot next"><svg width="8" height="10" viewBox="0 0 8 10"><path d="M2 1 6 5 2 9" fill="none" stroke="#888" stroke-width="1.6"/></svg></span>
  </div>
</section>

<footer class="site-footer">
  <div class="foot-brand">CORVEL<br>AUTOMOTIVE</div>
  <div class="partners"><i></i><i></i><i style="width:50px"></i><i style="width:92px;margin-left:-42px"></i></div>

  <h4 class="foot-heading" style="left:367px">Quick Links.</h4>
  <ul class="quick-links">
    <li>Home</li><li>About Us</li><li>Services</li><li>Gallery</li><li>Testimonials</li><li>Contact Us</li>
  </ul>

  <h4 class="foot-heading" style="left:514px">Contact Us</h4>
  <ul class="contact-list">
    <li style="top:0"><span class="ic"><svg width="14" height="14" viewBox="0 0 14 14"><path d="M7 1C4.5 1 3 3 3 5c0 3 4 8 4 8s4-5 4-8c0-2-1.5-4-4-4z" fill="#333"/><circle cx="7" cy="5" r="1.4" fill="#d9d9d9"/></svg></span><span>418 Ridgeway Court #3<br>Brookdale, TX 75900</span></li>
    <li style="top:47px"><span class="ic"><svg width="14" height="14" viewBox="0 0 24 24"><path d="M6 3 9 3 11 8 8 10C9.5 13 11 14.5 14 16L16 13 21 15 21 18C21 19.5 19.5 21 18 21 10 20 4 14 3 6 3 4.5 4.5 3 6 3Z" fill="#333"/></svg></span><span><span class="label">OFFICE:</span> 555.318.4720<br><span class="label">Phone:</span> 555.206.8814</span></li>
    <li style="top:110px"><span class="ic"><svg width="14" height="14" viewBox="0 0 14 14"><rect x="1.5" y="3" width="11" height="8" fill="none" stroke="#333" stroke-width="1.4"/><path d="M1.5 3 7 8 12.5 3" fill="none" stroke="#333" stroke-width="1.4"/></svg></span><span>hello@corvelauto.example</span></li>
    <li style="top:157px"><span class="ic"><svg width="14" height="14" viewBox="0 0 14 14"><circle cx="7" cy="7" r="5.5" fill="none" stroke="#333" stroke-width="1.4"/><path d="M7 4v3l2 1.5" fill="none" stroke="#333" stroke-width="1.4"/></svg></span><span><span class="label">Hours of Operation:</span> M-F 8:30-6pm</span></li>
  </ul>

  <div class="map" role="img" aria-label="Street map showing the shop location"></div>
  <div class="socials"><i></i><i></i><i></i></div>
</footer>

<div class="copyright">
  <svg class="abs" style="left:0;top:0" width="1200" height="43" viewBox="0 0 1200 43"><polygon points="336,0 1200,0 1200,43 310,43" fill="#e3020f"/><polygon points="318,0 328,0 302,43 292,43" fill="#d9d9d9"/></svg>
  <p>Copyright © 2024 Corvel Automotive LLC. All Rights Reserved.</p>
</div>

</body>
</html>
```